Vellmore Family Law, legal technician needs a website and design

I need a website for a family law practice. I specialize in collaborative law, unbundled services, and mediation. The website must contain my company logo (file attached), and the website must be a mixture of my personality and my profession. I have attached additional information to explain my personality and profession.

Target Market(s)

Lower through middle-class (income level up to $200,000 per year)

Coding

Coded - Design and coding required

Number of Pages Required

1 page

Requirements
Must have
• Must have enough pages to cover required content. I submitted below some content about the collaborative law process. All of the content is not necessary. However, the website must have enough content to clearly describe the services I offer. Use your professionalism and judgment regarding font, font size, etc.

```html
<!DOCTYPE html>
<html lang="en">
<head>
<meta charset="utf-8">
<title>Vellmore Family Law</title>
<link rel="stylesheet" href="https://fonts.googleapis.com/css2?family=Cinzel:wght@400;500&family=Roboto:wght@400;500;700&display=swap">
<style>
:root{
  --olive:#8b7b3b;
  --olive-dark:#6f6230;
  --lime:#b3aa3c;
  --ink:#222;
  --text:#6b6b6b;
  --gray-bg:#f3f3f3;
  --footer:#3c3c3c;
  --white:#fff;
  --star:#e0a100;
}
*{box-sizing:border-box;margin:0;padding:0}
html,body{width:1200px;height:4415px;overflow:hidden}
body{font-family:'Roboto',Arial,sans-serif;color:var(--text);background:var(--white);position:relative}
.abs{position:absolute}
.serif{font-family:'Cinzel',Georgia,serif;font-weight:400}
.btn{position:absolute;display:flex;align-items:center;justify-content:center;gap:8px;background:var(--olive);color:var(--white);font:700 13px 'Roboto',Arial,sans-serif;text-transform:uppercase;border-radius:3px;height:44px;width:188px}
.btn .arrow{width:13px;height:13px;border-radius:50%;background:var(--white);position:relative}
.btn .arrow::after{content:"";position:absolute;left:4px;top:3.5px;border-left:5px solid var(--olive);border-top:3px solid transparent;border-bottom:3px solid transparent}
.section-title{position:absolute;left:0;width:1200px;text-align:center;font-family:'Cinzel',Georgia,serif;font-size:34px;color:var(--ink);letter-spacing:1px}

/* top bar */
.topbar{position:absolute;top:0;left:0;width:1200px;height:48px;background:var(--lime);color:var(--white);font:700 14px 'Roboto',Arial,sans-serif}
.topbar .phone-ic{position:absolute;left:675px;top:8px;width:32px;height:32px;border:2px solid var(--white);border-radius:50%}
.topbar .txt{position:absolute;left:731px;top:15px}

/* nav */
.nav{position:absolute;top:48px;left:0;width:1200px;height:77px;background:var(--white)}
.brand{position:absolute;display:flex;align-items:center;gap:10px;font-family:'Cinzel',Georgia,serif;color:var(--olive);line-height:1.05}
.brand .mark{width:40px;height:40px;border:2px solid var(--olive)}
.nav .brand{left:111px;top:16px;font-size:17px}
.menu{position:absolute;top:31px;font:700 13px 'Roboto',Arial,sans-serif;color:var(--ink)}
.nav .btn{left:900px;top:19px;height:41px;width:187px}

/* hero */
.hero{position:absolute;top:125px;left:0;width:1200px;height:552px;background:linear-gradient(90deg,#6c6355 0%,#8c8478 30%,#7a7368 55%,#5d5a55 80%,#4f4d4a 100%)}
.hero h1{position:absolute;top:230px;left:0;width:1200px;text-align:center;color:var(--white);font-family:'Cinzel',Georgia,serif;font-weight:400;font-size:28px;line-height:47px;letter-spacing:1px}
.hero .btn{left:507px;top:394px;width:187px}
.dots{position:absolute;display:flex;gap:5px}
.dots i{width:9px;height:9px;border-radius:50%;background:var(--white);border:1px solid var(--white)}
.dots i.off{background:transparent}

/* about */
.about-frame{position:absolute;left:103px;top:780px;width:428px;height:391px;background:var(--olive)}
.photo{position:absolute;background:linear-gradient(135deg,#c9c5bd,#8d8a84)}
.about-photo{left:120px;top:797px;width:429px;height:389px;background:linear-gradient(135deg,#e6e3dd,#9d9a93 60%,#6b6a66)}
.about h2,.rfl h2{position:absolute;font-family:'Cinzel',Georgia,serif;font-weight:400;font-size:33px;color:var(--ink);letter-spacing:1px}
.body-copy{position:absolute;font-size:13.5px;line-height:29px;color:var(--text)}

/* offer */
.offer{position:absolute;top:1308px;left:0;width:1200px;height:495px;background:var(--gray-bg)}
.offer-card{position:absolute;top:173px;height:235px}
.offer-card .label{position:absolute;left:0;width:100%;text-align:center;color:var(--white);font-family:'Cinzel',Georgia,serif;font-size:16px;letter-spacing:.5px}
.offer-card .ic{position:absolute;left:50%;margin-left:-20px;width:40px;height:32px;border:2px solid var(--white);border-radius:4px}
.corner{position:absolute;width:22px;height:22px;border-color:var(--olive);border-style:solid;border-width:0}

/* rfl */
.rfl-frame{position:absolute;left:629px;top:1923px;width:100px;height:100px;background:var(--olive)}
.rfl-outline{position:absolute;left:661px;top:1955px;width:436px;height:333px;border:2px solid var(--olive)}
.rfl-photo{left:645px;top:1939px;width:438px;height:338px;background:linear-gradient(120deg,#b7b1a6,#6f6e6a 50%,#a4a19a)}
.play{position:absolute;left:846px;top:2089px;width:40px;height:40px;border-radius:50%;background:var(--white)}
.play::after{content:"";position:absolute;left:11px;top:11px;width:18px;height:18px;border-radius:50%;background:var(--olive)}
.play::before{content:"";position:absolute;left:18px;top:15px;border-left:8px solid var(--white);border-top:5px solid transparent;border-bottom:5px solid transparent;z-index:1}

/* brands */
.brands{position:absolute;top:2410px;left:0;width:1200px;height:298px;background:linear-gradient(90deg,#8a7a3a,#9a8a48 50%,#86773a)}
.brand-box{position:absolute;top:130px;width:189px;height:98px;background:var(--white);display:flex;align-items:center;justify-content:center;gap:8px;font-family:'Cinzel',Georgia,serif;font-size:15px;color:#333}
.brand-box .sq{width:14px;height:14px;background:#333}

/* blog */
.blog-img{position:absolute;top:2890px;width:317px;height:219px}
.blog-title{position:absolute;top:3143px;width:300px;font:700 12.5px 'Roboto',Arial,sans-serif;line-height:23px;color:var(--ink);text-transform:uppercase}
.blog-meta{position:absolute;top:3236px;width:295px;height:30px;border-bottom:1px solid #e3e3e3;font-size:12.5px;color:#777}
.blog-meta span{position:absolute;top:0}
.blog-meta .i{width:12px;height:11px;background:#b8ad85;border-radius:2px}

/* testimonials */
.testi{position:absolute;top:3370px;left:0;width:1200px;height:538px;background:linear-gradient(90deg,#8a7a3a,#9b8c4c 50%,#8a7a3a)}
.t-card{position:absolute;top:165px;height:233px;background:var(--white)}
.t-avatar{position:absolute;top:44px;width:115px;height:144px;border:5px solid #eee;background:linear-gradient(180deg,#b9b3a6,#5d5a53)}
.stars{position:absolute;top:46px;color:var(--star);font-size:19px;letter-spacing:3px}
.quote{position:absolute;top:28px;font:700 60px Georgia,serif;color:var(--olive);line-height:1}
.t-text{position:absolute;top:84px;font-size:13.5px;line-height:26px;color:#888;text-align:justify}
.t-name{position:absolute;top:199px;font:700 12.5px 'Roboto',Arial,sans-serif;color:var(--olive);text-transform:uppercase}

/* footer */
.footer{position:absolute;top:3908px;left:0;width:1200px;height:507px;background:var(--footer);color:#ddd;font-size:13px}
.f-head{position:absolute;top:207px;font:700 13px 'Roboto',Arial,sans-serif;color:var(--white);text-decoration:underline;text-transform:uppercase}
.f-list{position:absolute;top:242px;list-style:none;line-height:32px;color:#ddd}
.f-list li::before{content:"» ";color:#ddd}
.f-ic{position:absolute;width:28px;height:28px;border:2px solid #ddd;border-radius:50%}
.social{position:absolute;top:394px;left:113px;display:flex;gap:8px}
.social i{width:33px;height:33px;border:2px solid #ddd;border-radius:50%}
</style>
</head>
<body>

<header>
  <div class="topbar">
    <div class="phone-ic"></div>
    <div class="txt">CALL US TOLL FREE - 24 HOURS &nbsp;: &nbsp; 1 800 555 0142</div>
  </div>
  <nav class="nav">
    <div class="brand"><span class="mark"></span><span>VELLMORE<br>FAMILY LAW</span></div>
    <span class="menu" style="left:360px">HOME</span>
    <span class="menu" style="left:430px">ABOUT US</span>
    <span class="menu" style="left:530px">OUR SERVICES</span>
    <span class="menu" style="left:657px">LATEST BLOG</span>
    <span class="menu" style="left:780px">CONTACT US</span>
    <a class="btn">Free Consultation <span class="arrow"></span></a>
  </nav>
</header>

<section class="hero" role="img" aria-label="Photo of a couple in conversation with a legal professional">
  <h1>VELLMORE FAMILY LAW, COLLABORATIVE<br>LAW &amp; UNBUNDLED LEGAL SERVICES<br>IN KING COUNTY, WASHINGTON STATE</h1>
  <a class="btn">Free Consultation <span class="arrow"></span></a>
  <div class="dots" style="left:572px;top:510px"><i></i><i></i><i class="off"></i><i></i><i></i></div>
</section>

<section class="about">
  <div class="about-frame"></div>
  <div class="photo about-photo" role="img" aria-label="Photo of lawyers reviewing documents at a meeting table"></div>
  <h2 style="left:610px;top:790px">ABOUT US</h2>
  <p class="body-copy" style="left:610px;top:845px;width:490px">Lorem ipsum dolor sit amet, consectetur adipiscing elit, sed do eiusmod tempor incididunt ut labore et dolore magna aliqua. Ut enim ad minveniam, quis nostrud exercitation ullamco laboris nisi ut aliquip ex ea commodo consequat. Duis aute irure dolor in reprehenderit in voluptate velit esscillum dolore eu fugiat nulla pariatur. Lorem ipsum dolor sit amconsect adipiscing elit, sed do eiusmod tempor incididunt ut labore et doloremagna aliqua. Ut enim ad minim veniam, quis nostrud exercitation ullamco laboris nisi ut aliquip ex ea commodo consequat. Duis aute irure dolor in reprehenderit in voluptate velit esse cillum dolore eu fugiat nulla pariatur.</p>
  <a class="btn" style="left:610px;top:1126px">Free Consultation <span class="arrow"></span></a>
</section>

<section class="offer">
  <h2 class="section-title" style="top:72px">WHAT WE OFFER</h2>
  <div class="offer-card" style="left:108px;width:317px;background:linear-gradient(135deg,#a69e90,#6a655c)" role="img" aria-label="Photo of a collaborative meeting around a table">
    <span class="ic" style="top:130px"></span>
    <span class="label" style="top:190px">COLLABORATIVE LAW</span>
  </div>
  <div class="offer-card" style="left:449px;width:302px">
    <span class="corner" style="left:0;top:0;border-left-width:3px;border-top-width:3px"></span>
    <span class="corner" style="right:0;top:0;border-right-width:3px;border-top-width:3px"></span>
    <span class="corner" style="left:0;bottom:0;border-left-width:3px;border-bottom-width:3px"></span>
    <span class="corner" style="right:0;bottom:0;border-right-width:3px;border-bottom-width:3px"></span>
    <div style="position:absolute;left:10px;top:12px;width:285px;height:212px;background:linear-gradient(135deg,#9d8d4f,#8b7b3b)" role="img" aria-label="Olive tinted photo of a business meeting">
      <span class="ic" style="top:60px"></span>
      <span class="label" style="top:118px">UNBUNDLED SERVICES</span>
      <span style="position:absolute;left:125px;top:150px;width:36px;height:2px;background:var(--white)"></span>
    </div>
  </div>
  <div class="offer-card" style="left:775px;width:317px;background:linear-gradient(135deg,#cfcbc3,#6e6a63)" role="img" aria-label="Photo of a mediation session">
    <span class="ic" style="top:140px"></span>
    <span class="label" style="top:190px">MEDIATION</span>
  </div>
</section>

<section class="rfl">
  <h2 style="left:111px;top:1930px">VELLMORE FAMILY LAW</h2>
  <p class="body-copy" style="left:111px;top:1983px;width:475px">Lorem ipsum dolor sit amet, consectetur adipiscing elit, sed do eiusmod tempor incididunt ut labore et dolore magna aliqua. Ut enim ad minveniam, quis nostrud exercitation ullamco laboris nisi ut aliquip ex ea commodo consequat. Duis aute irure dolor in reprehenderit in voluptate velit esscillum dolore eu fugiat nulla pariatur. Lorem ipsum dolor sit amconsect adipiscing elit, sed do eiusmod tempor incididunt ut labore et doloremagna aliqua. Ut enim ad minim veniam, quis nostrud exercitation ullamco laboris nisi ut aliquip ex ea commodo consequat.</p>
  <a class="btn" style="left:111px;top:2233px">Free Consultation <span class="arrow"></span></a>
  <div class="rfl-frame"></div>
  <div class="rfl-outline"></div>
  <div class="photo rfl-photo" role="img" aria-label="Video still of three colleagues discussing a case"></div>
  <div class="play"></div>
</section>

<section class="brands" role="img" aria-label="Olive tinted background photo of an office meeting">
  <h2 class="section-title" style="top:65px;color:var(--white)">OUR BRANDS</h2>
  <div class="brand-box" style="left:111px"><span class="sq"></span>Harlow Legal</div>
  <div class="brand-box" style="left:309px"><span class="sq"></span>Brightstone</div>
  <div class="brand-box" style="left:506px"><span class="sq"></span>Quill &amp; Cole</div>
  <div class="brand-box" style="left:703px"><span class="sq"></span>Ridgeway</div>
  <div class="brand-box" style="left:900px"><span class="sq"></span>Elmstead Law</div>
</section>

<section class="blog">
  <h2 class="section-title" style="top:2806px">LATEST BLOG</h2>
  <div class="blog-img" style="left:108px;background:linear-gradient(135deg,#e4e4e2,#8d8c89)" role="img" aria-label="Photo of a handshake at a client meeting"></div>
  <div class="blog-img" style="left:442px;background:linear-gradient(135deg,#d8d2c8,#7a7368)" role="img" aria-label="Photo of two colleagues reviewing paperwork"></div>
  <div class="blog-img" style="left:775px;background:linear-gradient(135deg,#b9bcc0,#5f6064)" role="img" aria-label="Photo of two professionals talking at a desk"></div>

  <h3 class="blog-title" style="left:120px">Lorem ipsum dolor sit amet, consect etur adipiscing elit, sed do eiusmod tempor incididunt</h3>
  <h3 class="blog-title" style="left:454px">Lorem ipsum dolor sit amet, consect etur adipiscing elit, sed do eiusmod tempor incididunt</h3>
  <h3 class="blog-title" style="left:787px">Lorem ipsum dolor sit amet, consect etur adipiscing elit, sed do eiusmod tempor incididunt</h3>

  <div class="blog-meta" style="left:117px"><span class="i" style="left:13px;top:2px"></span><span style="left:44px">Mar 01 , 2021</span><span class="i" style="left:168px;top:2px;border-radius:50%"></span><span style="left:199px">No Comments</span></div>
  <div class="blog-meta" style="left:451px"><span class="i" style="left:13px;top:2px"></span><span style="left:44px">Mar 01 , 2021</span><span class="i" style="left:168px;top:2px;border-radius:50%"></span><span style="left:199px">No Comments</span></div>
  <div class="blog-meta" style="left:784px"><span class="i" style="left:13px;top:2px"></span><span style="left:44px">Mar 01 , 2021</span><span class="i" style="left:168px;top:2px;border-radius:50%"></span><span style="left:199px">No Comments</span></div>
</section>

<section class="testi" role="img" aria-label="Olive tinted background photo of a consultation">
  <h2 class="section-title" style="top:67px;color:var(--white)">WHAT OUR CLIENTS SAY</h2>
  <div class="t-card" style="left:113px;width:478px">
    <div class="t-avatar" style="left:34px" role="img" aria-label="Client portrait"></div>
    <div class="stars" style="left:190px">★★★★★</div>
    <div class="quote" style="left:405px">“</div>
    <p class="t-text" style="left:190px;width:240px">Et harum quidem rerum facilis est et expedita distinctio. Nam libero tempore, cum soluta nobis est eligendi optio cumque.</p>
    <div class="t-name" style="left:327px">- Mara Tollin</div>
  </div>
  <div class="t-card" style="left:614px;width:473px">
    <div class="t-avatar" style="left:34px" role="img" aria-label="Client portrait"></div>
    <div class="stars" style="left:185px">★★★★★</div>
    <div class="quote" style="left:404px">“</div>
    <p class="t-text" style="left:190px;width:240px">Temporibus autem quibusdam et aut officiis debitis aut rerum necessitatibus saepe eveniet ut et voluptates.</p>
    <div class="t-name" style="left:332px">- Devon Oakes</div>
  </div>
  <div class="dots" style="left:579px;top:456px"><i></i><i></i><i class="off"></i><i></i></div>
</section>

<footer class="footer">
  <div class="abs" style="left:178px;top:56px;font:700 20px 'Roboto',Arial,sans-serif;color:var(--white)">CONTACT US</div>
  <div class="abs" style="left:339px;top:55px;width:504px;height:50px;background:var(--white);color:#777;padding:17px 0 0 57px;font-size:13px">Enter Your Email</div>
  <span class="abs" style="left:365px;top:75px;width:14px;height:10px;border:1.5px solid var(--olive)"></span>
  <div class="abs" style="left:854px;top:55px;width:142px;height:50px;background:var(--olive);color:var(--white);font:700 15px 'Roboto',Arial,sans-serif;display:flex;align-items:center;justify-content:center">EMAIL US</div>
  <div class="abs" style="left:111px;top:153px;width:976px;height:1px;background:#888"></div>

  <div class="brand" style="left:113px;top:192px;font-size:24px;color:var(--white)"><span class="mark" style="border-color:var(--white);width:48px;height:48px"></span><span>VELLMORE<br>FAMILY LAW</span></div>
  <p class="abs" style="left:113px;top:288px;width:270px;line-height:26px;color:#eee">Vellmore Family Law, collaborative law and unbundled legal services in King County, Washington state</p>
  <div class="social" aria-label="Social media links"><i></i><i></i><i></i><i></i></div>

  <div class="f-head" style="left:439px">Contact Us</div>
  <span class="f-ic" style="left:441px;top:250px"></span>
  <p class="abs" style="left:493px;top:248px;line-height:22px">238 , Lorem Ipsum Dolor<br>United States</p>
  <span class="f-ic" style="left:441px;top:323px"></span>
  <p class="abs" style="left:493px;top:329px">info@vellmorelaw.com</p>
  <span class="f-ic" style="left:441px;top:384px"></span>
  <p class="abs" style="left:493px;top:388px;font-size:19px;color:var(--white)">1 800 555 0142</p>

  <div class="f-head" style="left:740px">Quick Links</div>
  <ul class="f-list" style="left:740px"><li>Home</li><li>About Us</li><li>Our Services</li><li>Blog</li><li>Our Team</li></ul>

  <div class="f-head" style="left:950px">Other Links</div>
  <ul class="f-list" style="left:950px"><li>Contact Us</li><li>FAQ</li><li>Help Service</li><li>Terms Of Use</li><li>Privacy Policy</li></ul>

  <div class="abs" style="left:111px;top:446px;width:976px;height:1px;background:#888"></div>
  <p class="abs" style="left:0;top:468px;width:1200px;text-align:center;color:#eee">© 2021 Vellmore Family Law. All Rights Reserved</p>
</footer>

</body>
</html>
```